Large Essential oil business needs a unique label design

We offer essential oil blends in various sizes with over 40+ blends. We want a unique design using our new logo.
Classy, easy to read and different than the other EO companies.
With over 40 blends all the ingredients must be l listed.
Warnings: discontinue use if irritation occurs, keep out of reach of children, for external use only unless working with a professional.
Certified Organic and Wild Harvested Essential Oils from all over the world. Pure therapeutic grade.
Would like area for bar code or bar code information if possible...
(see pictures)
5 ml roll on 3 cm H 6 cm Diameter
10 ml roll 4 cm H 6.75 diameter
30 ml roll 4 cm H 10.25 diameter

Diffuser bottles
5 ml 2.25 H 7.5 cm D
10 ml 2.25 H 8.25 D
30 ml 4 cm H 10.25 D

Target Market(s)

retail, health and wellness, all audiences.

Industry/Entity Type

Health And Wellness

Contact Information for Business Card

daphne orlett founder/blender
Kimberley/Fernie, B.C. Canada mistwillowbrook@examplemail.com
(250)381 6094
mistwillowbrook.example

Font styles to use
Decorative

Colors
ec1f27

Requirements
Must have
• Blend name, all ingredients, warnings, instructions, logo,
• 5 ml/.17 fl oz
• 10 ml/.33 fl oz
• 30 ml/1 fl oz
• EXAMPLE BLEND:
• Calm Harbor
• Sleep and Insomnia
• Organic & Wild Crafted Oils of: orange, marjoram, clary sage, melissa, in olive oil
• Usage: roll on soles of feet prior to bed or as needed. Top of shoulders/navel area.
• Discontinue use if irritation occurs, keep out of reach of children, for external use only unless working with a qualified professional.
• Organic and Wild Harvested Oils sourced Globally. 100% Therapeutic Grade
Nice to have
• wood design somehow, unique

```html
<!DOCTYPE html>
<html lang="en">
<head>
<meta charset="utf-8">
<title>Calm Harbor – Roll-on Label Sheet</title>
<link href="https://fonts.googleapis.com/css2?family=Didact+Gothic&family=Josefin+Sans:wght@300&display=swap" rel="stylesheet">
<style>
  :root {
    --wood-light: #f4f4f3;
    --wood-mid: #e4e4e2;
    --plank-line: rgba(150,150,150,0.18);
    --ink: #5b5b5b;
    --brand-red: #8f1b1d;
    --band-red: #8c1a1c;
    --paper: #ffffff;
    --floral-a: #e9e9e7;
    --floral-b: #d6d6d3;
  }
  * { box-sizing: border-box; margin: 0; padding: 0; }
  html, body { width: 1200px; height: 997px; overflow: hidden; background: var(--paper); }
  body { font-family: "Didact Gothic", sans-serif; color: var(--ink); }

  .sheet { width: 1200px; height: 997px; display: flex; flex-direction: column; justify-content: space-between; }

  .label {
    position: relative;
    width: 1200px;
    height: 480px;
    overflow: hidden;
    background:
      repeating-linear-gradient(90deg, transparent 0 118px, var(--plank-line) 118px 120px),
      linear-gradient(100deg, var(--wood-light), var(--wood-mid) 45%, var(--wood-light) 70%, var(--wood-mid));
  }

  .ingredients, .usage {
    position: absolute; left: 16px; width: 290px;
    font-size: 14.5px; line-height: 1.45; text-align: justify;
  }
  .ingredients { top: 8px; }
  .usage { top: 84px; }
  .sourcing {
    position: absolute; left: 120px; top: 142px; width: 150px;
    font-size: 13px; line-height: 1.35; text-align: center;
  }
  .barcode-area {
    position: absolute; left: 20px; top: 204px; width: 122px; height: 92px;
    background: var(--paper);
  }
  .grade {
    position: absolute; left: 220px; top: 206px; width: 110px;
    font-size: 14px; line-height: 1.4;
  }

  .brand {
    position: absolute; left: 480px; top: 24px; width: 240px; height: 232px;
    display: flex; flex-direction: column; align-items: center; justify-content: center; gap: 14px;
  }
  .brand-dot { width: 22px; height: 22px; border-radius: 50%; background: var(--brand-red); }
  .brand-name {
    font-family: "Didact Gothic", sans-serif;
    color: var(--brand-red); font-size: 25px; line-height: 1.25;
    text-align: center; letter-spacing: 1px; text-transform: uppercase;
  }
  .purity {
    position: absolute; left: 0; width: 1200px; top: 262px; text-align: center;
    font-size: 19px; padding-right: 0;
  }
  .purity span { display: inline-block; margin-left: 0; position: relative; left: 0; }

  .name-band {
    position: absolute; left: 0; top: 294px; width: 1200px; height: 42px;
    background: var(--band-red);
  }
  .blend-name {
    position: absolute; left: 0; width: 930px; top: 4px; text-align: right; padding-right: 430px;
    font-family: "Josefin Sans", sans-serif; font-weight: 300;
    color: var(--paper); font-size: 31px; letter-spacing: 2px;
  }
  .blend-size {
    position: absolute; left: 712px; top: 12px;
    color: var(--paper); font-size: 15px;
    transform: rotate(-90deg); transform-origin: center;
  }

  .floral-border {
    position: absolute; left: 0; top: 344px; width: 1200px; height: 118px;
    background: linear-gradient(180deg, var(--floral-a), var(--floral-b) 70%, var(--floral-a));
    opacity: 0.85;
  }

  .warnings {
    position: absolute; left: 892px; top: 14px; width: 294px;
    font-size: 16px; line-height: 1.4; text-align: justify;
  }
  .warnings p + p { margin-top: 10px; }
</style>
</head>
<body>
<main class="sheet">
  <section class="label">
    <p class="ingredients">Organic &amp; wild crafted oils of: orange, marjoram, clary sage, melissa, in olive oil</p>
    <p class="usage">Usage: roll on soles of feet prior to bed or as needed. Top of shoulders/navel area.</p>
    <p class="sourcing">Organic and Wild Harvested Oils sourced Globally</p>
    <div class="barcode-area"></div>
    <p class="grade">100% Pure Therapeutic Grade.</p>

    <div class="brand">
      <div class="brand-dot"></div>
      <p class="brand-name">Mist Willow Brook<br>Essential Oil Co.</p>
    </div>
    <p class="purity"><span>100% Pure Oil</span></p>

    <div class="name-band">
      <p class="blend-name">Calm Harbor</p>
      <p class="blend-size">15ml</p>
    </div>
    <div class="floral-border" role="img" aria-label="Hand-drawn border of wildflowers and herbs"></div>

    <div class="warnings">
      <p>Discontinue use if irritation occurs, keep out of reach of children, for external use only unless working with a qualified professional.</p>
      <p>Warnings: discontinue use if irritation occurs, keep out of reach of children, for external use only unless working with a professional.</p>
    </div>
  </section>

  <section class="label">
    <p class="ingredients">Organic &amp; wild crafted oils of: orange, marjoram, clary sage, melissa, in olive oil</p>
    <p class="usage">Usage: roll on soles of feet prior to bed or as needed. Top of shoulders/navel area.</p>
    <p class="sourcing">Organic and Wild Harvested Oils sourced Globally</p>
    <div class="barcode-area"></div>
    <p class="grade">100% Pure Therapeutic Grade.</p>

    <div class="brand">
      <div class="brand-dot"></div>
      <p class="brand-name">Mist Willow Brook<br>Essential Oil Co.</p>
    </div>
    <p class="purity"><span>100% Pure Oil</span></p>

    <div class="name-band">
      <p class="blend-name">Calm Harbor</p>
      <p class="blend-size">15ml</p>
    </div>
    <div class="floral-border" role="img" aria-label="Hand-drawn border of wildflowers and herbs"></div>

    <div class="warnings">
      <p>Discontinue use if irritation occurs, keep out of reach of children, for external use only unless working with a qualified professional.</p>
      <p>Warnings: discontinue use if irritation occurs, keep out of reach of children, for external use only unless working with a professional.</p>
    </div>
  </section>
</main>
</body>
</html>
```